Business Card Design

I need business cards designed for a new company i have started that makes cakes, particularly themed kids cakes with a really modern design and I would like to have my business cards reflect this. I have attached some photos of cakes I have made and would like some to be used.

Industry/Entity Type

Business

Contact Information for Business Card

Business Name: Tarts and Treats by Maren
Mobile: 0492 815 063
email: maren@tartsandtreatsbymaren.example.au
Instagram: instagram.com/tartsandtreatsbymaren/
Facebook: fb.me/tartsandtreatsbymaren

Colors
e667a6
b768aa
3276b5

Requirements
Must have
• Business Name: Tarts and Treats by Maren
• Mobile: 0492 815 063
• email: maren@tartsandtreatsbymaren.example.au
• Instagram: instagram.com/tartsandtreatsbymaren/
• Facebook: fb.me/tartsandtreatsbymaren
Nice to have
• 2 to 3 pictures of my cakes

```html
<!DOCTYPE html>
<html lang="en">
<head>
<meta charset="utf-8">
<title>Tarts and Treats by Maren — Business Card</title>
<link rel="stylesheet" href="https://fonts.googleapis.com/css2?family=Open+Sans:wght@400;600&display=swap">
<style>
  :root {
    --pink: #e667a6;
    --plum: #b768aa;
    --blue: #3276b5;
    --blue-light: #4f8fcb;
    --blue-dark: #245f98;
    --ink: #4a4a4a;
    --paper: #ffffff;
    --backdrop: #ece9e4;
  }
  * { box-sizing: border-box; margin: 0; padding: 0; }
  html, body {
    width: 1200px;
    height: 843px;
    overflow: hidden;
    background: var(--backdrop);
    font-family: "Open Sans", sans-serif;
  }
  .sheet {
    width: 1200px;
    height: 843px;
    display: flex;
    align-items: center;
    justify-content: center;
    gap: 50px;
  }
  .card {
    position: relative;
    width: 530px;
    height: 303px;
    border-radius: 4px;
    overflow: hidden;
    box-shadow: 0 6px 20px rgba(0, 0, 0, 0.18);
  }

  /* Back side */
  .card--back {
    background: linear-gradient(160deg, var(--blue-light) 0%, var(--blue) 55%, var(--blue-dark) 100%);
    display: flex;
    align-items: center;
    justify-content: center;
  }
  .wordmark {
    font-family: "Open Sans", sans-serif;
    font-weight: 600;
    text-align: center;
    line-height: 1.15;
  }
  .card--back .wordmark {
    color: var(--paper);
    font-size: 30px;
  }

  /* Front side */
  .card--front { background: var(--paper); }
  .drip {
    position: absolute;
    inset: 0;
    width: 100%;
    height: 100%;
  }
  .drip path { fill: var(--pink); }
  .front-content {
    position: absolute;
    left: 262px;
    top: 38px;
    right: 22px;
  }
  .card--front .wordmark {
    color: var(--pink);
    font-size: 24px;
    text-align: left;
  }
  .rule {
    height: 1px;
    width: 90%;
    background: var(--plum);
    opacity: 0.5;
    margin: 14px 0 12px;
  }
  .person {
    color: var(--pink);
    font-size: 17px;
    letter-spacing: 0.06em;
    text-transform: uppercase;
  }
  .person .role {
    font-size: 11px;
    letter-spacing: 0.02em;
    text-transform: none;
    margin-left: 4px;
  }
  .contacts {
    list-style: none;
    margin-top: 12px;
    font-size: 11px;
    color: var(--ink);
    line-height: 1.85;
  }
  .contacts .label { color: var(--pink); }
  .contacts .mark {
    display: inline-block;
    width: 9px;
    height: 9px;
    background: var(--plum);
    border-radius: 2px;
    margin-right: 6px;
    vertical-align: -1px;
  }
</style>
</head>
<body>
  <main class="sheet">
    <section class="card card--back" aria-label="Card back">
      <p class="wordmark">Tarts and Treats<br>by Maren</p>
    </section>

    <section class="card card--front" aria-label="Card front">
      <svg class="drip" viewBox="0 0 530 303" preserveAspectRatio="none" aria-hidden="true">
        <path d="M0 0 H160 C188 0 192 32 176 56 C160 82 214 74 222 104 C230 134 168 138 176 168 C184 198 244 194 244 228 C244 258 182 254 178 278 C175 294 182 303 182 303 H0 Z"/>
      </svg>
      <div class="front-content">
        <p class="wordmark">Tarts and Treats<br>by Maren</p>
        <div class="rule"></div>
        <p class="person">Lena Hart<span class="role">– CEO/Founder</span></p>
        <ul class="contacts">
          <li><span class="label">Mob:</span> 0492 815 063</li>
          <li><span class="mark"></span>instagram.com/tartsandtreatsbymaren/</li>
          <li><span class="mark"></span>fb.me/tartsandtreatsbymaren</li>
          <li>maren@tartsandtreatsbymaren.example.au</li>
        </ul>
      </div>
    </section>
  </main>
</body>
</html>
```